Dwelvano - "Where Pest Control is Free for Life..." Please see pitch deck...

Project goal, that this is a reusable template, not a one-off card
Brand and design direction, follow the logo, use the brand palette (with a color swatch table), typography and layout guidance
The John Doe placeholder content as a clean field-by-field table (name, title, company, address, office, cell, fax, email, dwelvano.com)
Print specs, 3.5 × 2 in trim, 0.125 in bleed, 300 DPI, CMYK, crop marks
Deliverables, layered editable PSD (your primary ask) plus vector .AI/.EPS and a press-ready PDF/X-1a, with fonts packaged
What you'll provide (logo, colors, fonts)
Process and sign-off, concept first, then full file package on approval.
Populate every field with this John Doe placeholder data so we can see the layout fully built out. We will replace it per person.
Name John Doe
Title Title / Position
Company Dwelvano
Address 123 Main Street, Suite 100, Tallahassee, FL 32301
Office (850) 555-0100
Cell (850) 555-0123
Fax (850) 555-0199
Email johndoe@dwelvano.com
Website dwelvano.com

We need the working, editable source files so we can update them ourselves, plus a ready-to-print export:
1. Photoshop (.PSD) — fully layered and editable, with each contact field on its own labeled text layer. This is the primary requested format.
2. Vector source — the press-standard editable format, Adobe Illustrator (.AI) and/or .EPS, since vector is preferred for crisp text and logos at print.
3. Print-ready PDF — press-quality (PDF/X-1a), CMYK, with bleed and crop marks, both sides.
4. Packaged fonts and links — include or list all fonts used, and package any linked assets so the files open correctly on our end.

Why both PSD and vector
The PSD covers our request directly and is easy for us to edit. Vector (.AI/.EPS) is what most commercial printers actually prefer for type and logos because it stays razor-sharp at any size. Providing both keeps us flexible no matter which printer we use. Have fun and keep it modern and cool the designer of the logo did a great job, see what you can do.

```html
<!DOCTYPE html>
<html lang="en">
<head>
<meta charset="utf-8">
<title>Dwelvano Business Card</title>
<link rel="stylesheet" href="https://fonts.googleapis.com/css2?family=Lato:wght@400;900&family=Encode+Sans+Condensed:wght@700&display=swap">
<style>
  :root {
    --stage: #e8e8e8;
    --navy: #0b1226;
    --navy-pattern: #111b31;
    --teal: #00b3c6;
    --white: #ffffff;
  }
  * { margin: 0; padding: 0; box-sizing: border-box; }
  html, body { width: 1200px; height: 960px; overflow: hidden; }
  body { background: var(--stage); position: relative; font-family: "Lato", sans-serif; }

  .card {
    position: absolute;
    width: 726px;
    height: 414px;
    background: var(--navy);
    overflow: hidden;
  }
  .card--front { left: 86px; top: 62px; }
  .card--back { left: 344px; top: 506px; }

  .wordmark {
    position: absolute;
    font-family: "Lato", sans-serif;
    font-weight: 900;
    color: var(--white);
    letter-spacing: -1px;
    line-height: 1;
  }
  .card--front .wordmark { left: 40px; top: 54px; font-size: 62px; }

  .brand-square {
    position: absolute;
    left: 548px;
    top: 58px;
    width: 100px;
    height: 100px;
    background: var(--teal);
    border-radius: 6px;
  }

  .name-band { position: absolute; left: 0; top: 192px; width: 726px; height: 60px; }
  .person-name {
    position: absolute;
    left: 41px;
    top: 200px;
    font-family: "Encode Sans Condensed", sans-serif;
    font-weight: 700;
    font-size: 35px;
    color: var(--navy);
    line-height: 40px;
  }
  .company-line {
    position: absolute;
    left: 237px;
    top: 209px;
    font-size: 19px;
    color: var(--white);
    line-height: 24px;
  }

  .contact { position: absolute; color: var(--white); font-size: 19px; line-height: 24px; }
  .contact-row { display: flex; align-items: center; height: 24.5px; }
  .contact-row svg { flex: none; fill: var(--teal); }
  .address { left: 42px; top: 263px; }
  .address svg { margin-right: 12px; }
  .phones { left: 43px; top: 306px; }
  .online { left: 459px; top: 306px; }
  .phones svg, .online svg { width: 18px; height: 18px; margin-right: 11px; }

  .back-pattern { position: absolute; inset: 0; background: var(--navy-pattern); opacity: 0.55; }
  .card--back .wordmark {
    left: 0; right: 0; top: 164px;
    text-align: center;
    font-size: 76px;
  }
</style>
</head>
<body>
  <section class="card card--front" aria-label="Business card front">
    <div class="wordmark">Dwelvano</div>
    <div class="brand-square"></div>

    <svg class="name-band" viewBox="0 0 726 60" aria-hidden="true">
      <polygon points="0,0 210,0 226,54 0,54" fill="#00b3c6"/>
      <rect x="0" y="54" width="726" height="5" fill="#00b3c6"/>
    </svg>
    <div class="person-name">John Doe</div>
    <div class="company-line">Company Dwelvano</div>

    <div class="contact address">
      <div class="contact-row">
        <svg width="18" height="28" viewBox="0 0 18 28" aria-hidden="true"><path d="M9 0C4 0 0 4 0 9c0 7 9 19 9 19s9-12 9-19C18 4 14 0 9 0zm0 13a4 4 0 1 1 0-8 4 4 0 0 1 0 8z"/></svg>
        <span>123 Main Street, Suite 100, Tallahassee, FL 32301</span>
      </div>
    </div>

    <div class="contact phones">
      <div class="contact-row">
        <svg viewBox="0 0 24 24" aria-hidden="true"><path d="M6.6 10.8a15 15 0 0 0 6.6 6.6l2.2-2.2c.3-.3.7-.4 1-.2 1.1.4 2.3.6 3.6.6.6 0 1 .4 1 1V20c0 .6-.4 1-1 1C10.6 21 3 13.4 3 4c0-.6.4-1 1-1h3.5c.6 0 1 .4 1 1 0 1.3.2 2.5.6 3.6.1.3 0 .7-.2 1z"/></svg>
        <span>(850) 555-0100</span>
      </div>
      <div class="contact-row">
        <svg viewBox="0 0 24 24" aria-hidden="true"><path d="M7 1h10a2 2 0 0 1 2 2v18a2 2 0 0 1-2 2H7a2 2 0 0 1-2-2V3a2 2 0 0 1 2-2zm0 3v14h10V4zm5 15.5a1 1 0 1 0 0 2 1 1 0 0 0 0-2z"/></svg>
        <span>(850) 555-0123</span>
      </div>
      <div class="contact-row">
        <svg viewBox="0 0 24 24" aria-hidden="true"><path d="M6 2h12v6H6zM3 9h18a1 1 0 0 1 1 1v7h-4v5H6v-5H2v-7a1 1 0 0 1 1-1zm5 7v4h8v-4z"/></svg>
        <span>(850) 555-0199</span>
      </div>
    </div>

    <div class="contact online">
      <div class="contact-row">
        <svg viewBox="0 0 24 24" aria-hidden="true"><path d="M2 10l10-7 10 7v11H2zm3 1l7 5 7-5z"/></svg>
        <span>johndoe@dwelvano.com</span>
      </div>
      <div class="contact-row">
        <svg viewBox="0 0 24 24" aria-hidden="true"><path d="M12 2a10 10 0 1 0 0 20 10 10 0 0 0 0-20zm6.9 9h-3a15 15 0 0 0-1.3-6 8 8 0 0 1 4.3 6zM12 4.1c.9 1.3 1.7 3.7 1.9 6.9h-3.8c.2-3.2 1-5.6 1.9-6.9zM9.4 5a15 15 0 0 0-1.3 6h-3a8 8 0 0 1 4.3-6zm-4.3 8h3a15 15 0 0 0 1.3 6 8 8 0 0 1-4.3-6zm6.9 6.9c-.9-1.3-1.7-3.7-1.9-6.9h3.8c-.2 3.2-1 5.6-1.9 6.9zm2.6-.9a15 15 0 0 0 1.3-6h3a8 8 0 0 1-4.3 6z"/></svg>
        <span>dwelvano.com</span>
      </div>
    </div>
  </section>

  <section class="card card--back" aria-label="Business card back">
    <div class="back-pattern" role="img" aria-label="Faint repeating brand pattern across the card background"></div>
    <div class="wordmark">Dwelvano</div>
  </section>
</body>
</html>
```